ORLA - Óptica Médica - web design and concept

Website concept - Create and develop our website design and structure. ORLA is an optical store chain, and we are looking to establish our web and digital concept. In attachment there are several pictures about our stores and our logo.

The website structure should be user friendly. Colors should be light and the design as simple and minimalist as possible. There are different variations of the logothat can be used, check the file.

The website will include optical collections and sun collections as an online store. Also, a medical menu should be considered in order for clients to schedule optometry appointments. There should also be a menu for client assistance where the clients can read about glass maintenance in our workshop.
Updates

Low design quality

Number of Pages Required

5+ page

Font styles to use
Serif
Sans Serif

Requirements
Must have
• Must be user-friendly and minimalist.
• Please USE PICTURES FROM THE BRANDS we sell: MERUN, BOSKA, PNW, KOLE, BAMPE
Nice to have
• Nice to inspire: ZEK glasses (see website https://ch.shopzek.com/en/)
• Nice to inspire: https://merun-eyewear.com/
• Nice to ispire: https://www.pnwglobe.com/en/
Should not have
• Hysteric colors and shapes

```html
<!DOCTYPE html>
<html lang="en">
<head>
<meta charset="utf-8">
<title>ORLA Óptica Médica – Product</title>
<link href="https://fonts.googleapis.com/css2?family=Heebo:wght@300;400;500;700&display=swap" rel="stylesheet">
<style>
:root{
  --ink:#1a1a1a;
  --muted:#555;
  --gold:#e8a23a;
  --band:#f5f5f7;
  --line:#e2e2e2;
  --black:#000;
  --white:#fff;
  --lens:#3d4a5c;
}
*{margin:0;padding:0;box-sizing:border-box}
html,body{width:1200px;height:2195px;overflow:hidden;background:var(--white)}
body{position:relative;font-family:"Heebo",sans-serif;color:var(--ink);font-weight:300}
.abs{position:absolute}
a{color:inherit;text-decoration:none}

/* header */
.social{left:161px;top:14px;display:flex;gap:8px}
.social i{display:block;width:11px;height:11px;border-radius:50%;background:var(--ink)}
.brand{left:0;width:1200px;top:32px;text-align:center;font-size:28px;font-weight:400;letter-spacing:6px}
.cart{left:820px;top:13px;font-size:11px;display:flex;align-items:center;gap:6px}
.phone{left:936px;top:13px;font-size:11px;display:flex;align-items:center;gap:6px}
.nav{top:104px;font-size:11px;font-weight:400}
.nav.active{color:var(--gold)}
.appoint{left:767px;top:102px;width:117px;height:22px;background:var(--black);color:var(--white);font-size:11px;font-weight:400;text-align:center;line-height:22px}
.crumb{left:161px;top:166px;font-size:12.5px}
.crumb span{color:var(--gold)}

/* product */
.product-photo{left:158px;top:211px;width:410px;height:409px;background:#ececec;display:flex;align-items:center;justify-content:center}
.product-photo div{width:360px;height:150px;border-radius:70px;background:radial-gradient(ellipse at center,#4d5a6e 0%,#2a3240 60%,#ececec 72%)}
.title{left:622px;top:206px;font-size:27px}
.code{left:622px;top:244px;font-size:11px;font-weight:400}
.price{left:622px;top:295px;font-size:26px}
.stock{left:622px;top:333px;font-size:12px;color:var(--gold)}
.label{font-size:12px;font-weight:400}
.select{height:28px;border:1px solid var(--black);display:flex;font-size:10.5px;font-weight:400}
.select span{flex:1;text-align:center;line-height:26px}
.select b{width:30px;background:var(--black);display:flex;align-items:center;justify-content:center}
.add{left:622px;top:565px;width:181px;height:53px;border:2px solid var(--black);text-align:center;line-height:49px;font-size:13px;font-weight:400}
.thumb{top:678px;width:66px;height:30px;border-radius:14px;background:linear-gradient(#5a677a,#2c3442)}

/* tabs */
.tab-a{left:161px;top:760px;width:186px;height:43px;background:var(--band);font-size:22px;padding:9px 0 0 42px}
.tab-b{left:347px;top:760px;width:221px;height:43px;background:var(--black);color:var(--white);clip-path:polygon(0 0,82% 0,100% 100%,13% 100%);font-size:22px;padding:9px 0 0 62px}
.specs{left:0;top:803px;width:1200px;height:221px;background:var(--band)}
.specs p{position:absolute;left:161px;font-size:17px}

/* related */
.heading{left:0;width:1200px;text-align:center;font-size:25px}
.rule{left:530px;width:140px;height:4px;border-top:1px solid var(--gold);border-bottom:1px solid var(--gold)}
.rel-img{top:1168px;width:150px;height:62px;border-radius:28px}
.rel-name{top:1261px;width:200px;text-align:center;font-size:16px}

/* features */
.feature{top:1371px;height:89px;width:287px;border:2px solid var(--line);display:flex;align-items:center;padding-left:56px;gap:12px}
.feature h4{font-size:17px;font-weight:300;color:#444}
.feature p{font-size:10.5px;font-weight:400}

/* brands */
.brands{left:0;top:1497px;width:1200px;height:164px;background:var(--band);border-top:1px solid var(--line)}
.mark{top:1562px;width:170px;text-align:center;font-size:24px;font-weight:500}

/* newsletter */
.news{left:303px;top:1772px;width:594px;height:70px;border:2px solid #d4d4d4;font-size:11px;font-weight:400;padding:31px 0 0 30px;color:#333}
.send{left:806px;top:1772px;width:91px;height:70px;border:2px solid var(--black);display:flex;align-items:center;justify-content:center;background:var(--white)}

/* footer */
.footer{left:0;top:1880px;width:1200px;height:315px;background:var(--black);color:var(--white)}
.footer .abs{color:var(--white)}
.f-brand{left:161px;top:1945px;font-size:20px;font-weight:400;color:var(--gold)!important;letter-spacing:3px}
.f-about{left:161px;top:1993px;width:160px;font-size:10.5px;line-height:13px;font-weight:400}
.f-head{font-size:13px;font-weight:700}
.f-list{list-style:none;font-size:10.5px;font-weight:400;line-height:16.4px}
.f-list li::before{content:"•";margin-right:8px}
.f-contact{font-size:10.5px;font-weight:400;display:flex;gap:7px}
.f-social{left:161px;top:2070px;display:flex;gap:8px}
.f-social i{display:block;width:10px;height:10px;border-radius:50%;background:var(--white)}
.divider{left:161px;top:2104px;width:880px;height:1px;background:#777}
.copy{top:2116px;font-size:12px;font-weight:400}
</style>
</head>
<body>

<header>
  <div class="abs social" aria-label="Social links"><i></i><i></i><i></i><i></i><i></i></div>
  <div class="abs brand">ORLA</div>
  <div class="abs cart">
    <svg width="10" height="11" viewBox="0 0 10 11"><rect x="1" y="4" width="8" height="7" fill="#1a1a1a"/><path d="M3 4V2.5a2 2 0 0 1 4 0V4" stroke="#1a1a1a" fill="none"/></svg>
    Your Cart &nbsp;( 0 )
  </div>
  <div class="abs phone">
    <svg width="10" height="10" viewBox="0 0 10 10"><path d="M2 0.5l2 2-1 1.3a6 6 0 0 0 3 3l1.3-1 2 2-1.3 1.7C4 9.5 0.5 6 .5 1.8z" fill="#1a1a1a"/></svg>
    +012-555-210-4
  </div>
  <nav>
    <a class="abs nav" style="left:315px">Home</a>
    <a class="abs nav active" style="left:365px">Online store</a>
    <a class="abs nav" style="left:446px">Company history</a>
    <a class="abs nav" style="left:549px">Medical section</a>
    <a class="abs nav" style="left:647px">Store</a>
    <a class="abs nav" style="left:692px">Contact Us</a>
    <a class="abs appoint">Make an Appoinment</a>
  </nav>
</header>

<main>
  <div class="abs crumb">Home / Online Store <span>/ Product Name</span></div>

  <div class="abs product-photo" role="img" aria-label="Photo of black aviator sunglasses with grey lenses"><div></div></div>

  <h1 class="abs title" style="font-weight:300">Product Name</h1>
  <div class="abs code">Code : 10B0C</div>
  <div class="abs price">30.00 EUR</div>
  <div class="abs stock">In Stock</div>

  <div class="abs label" style="left:622px;top:380px">Colour</div>
  <div class="abs select" style="left:622px;top:402px;width:99px"><span>Black</span><b><svg width="10" height="8"><path d="M0 0h10L5 8z" fill="#fff"/></svg></b></div>
  <div class="abs label" style="left:745px;top:380px">Size</div>
  <div class="abs select" style="left:745px;top:402px;width:99px"><span>Medium</span><b><svg width="10" height="8"><path d="M0 0h10L5 8z" fill="#fff"/></svg></b></div>
  <div class="abs label" style="left:622px;top:462px">QTY</div>
  <div class="abs select" style="left:622px;top:485px;width:99px"><span>1</span><b><svg width="10" height="8"><path d="M0 0h10L5 8z" fill="#fff"/></svg></b></div>

  <div class="abs add">ADD TO CART</div>

  <svg class="abs" style="left:117px;top:680px" width="14" height="26"><path d="M13 1L2 13l11 12" stroke="#1a1a1a" stroke-width="2" fill="none"/></svg>
  <div class="abs thumb" style="left:175px" role="img" aria-label="Sunglasses thumbnail"></div>
  <div class="abs thumb" style="left:277px" role="img" aria-label="Sunglasses thumbnail"></div>
  <div class="abs thumb" style="left:380px" role="img" aria-label="Sunglasses thumbnail"></div>
  <div class="abs thumb" style="left:484px" role="img" aria-label="Sunglasses thumbnail"></div>
  <svg class="abs" style="left:584px;top:680px" width="14" height="26"><path d="M1 1l11 12L1 25" stroke="var(--gold)" stroke-width="2" fill="none"/></svg>

  <div class="abs tab-a">Discription</div>
  <div class="abs tab-b">Loream</div>
  <section class="abs specs">
    <p style="top:44px">SIZE: MEDIUM</p>
    <p style="top:87px">MEASUREMENTS - 53x20x148</p>
    <p style="top:130px">SWISS DESIGN</p>
    <p style="top:174px">HANDMADE IN</p>
  </section>

  <h2 class="abs heading" style="top:1068px;font-weight:300">Related Product</h2>
  <div class="abs rule" style="top:1104px"></div>
  <svg class="abs" style="left:76px;top:1203px" width="22" height="40"><path d="M20 1L2 20l18 19" stroke="#1a1a1a" stroke-width="2" fill="none"/></svg>
  <div class="abs rel-img" style="left:166px;background:linear-gradient(#4a5a45,#2e3a2c)" role="img" aria-label="Aviator sunglasses with green lenses"></div>
  <div class="abs rel-img" style="left:406px;background:linear-gradient(#b2662a,#7a3e14)" role="img" aria-label="Tortoiseshell optical frames"></div>
  <div class="abs rel-img" style="left:641px;background:linear-gradient(#5a677a,#2c3442)" role="img" aria-label="Sunglasses with grey lenses"></div>
  <div class="abs rel-img" style="left:882px;background:linear-gradient(#2a2a2a,#000)" role="img" aria-label="Black square sunglasses"></div>
  <div class="abs rel-name" style="left:141px">Product Name</div>
  <div class="abs rel-name" style="left:381px">Product Name</div>
  <div class="abs rel-name" style="left:616px">Product Name</div>
  <div class="abs rel-name" style="left:857px">Product Name</div>
  <svg class="abs" style="left:1101px;top:1203px" width="22" height="40"><path d="M2 1l18 19L2 39" stroke="var(--gold)" stroke-width="2" fill="none"/></svg>

  <div class="abs feature" style="left:165px;padding-left:56px">
    <svg width="26" height="30" viewBox="0 0 26 30"><circle cx="13" cy="12" r="10" stroke="#1a1a1a" stroke-width="2" fill="none"/><path d="M13 22v6M7 28h12" stroke="#1a1a1a" stroke-width="2"/></svg>
    <div><h4>Free Shipping</h4><p>Lorem Ipsum is dummy text.</p></div>
  </div>
  <div class="abs feature" style="left:459px;padding-left:56px">
    <svg width="30" height="30" viewBox="0 0 30 30"><circle cx="15" cy="15" r="10" stroke="#1a1a1a" stroke-width="2" fill="none"/><rect x="2" y="13" width="5" height="8" fill="#1a1a1a"/><rect x="23" y="13" width="5" height="8" fill="#1a1a1a"/></svg>
    <div><h4>Premium Support</h4><p>24/7 Customer service</p></div>
  </div>
  <div class="abs feature" style="left:752px;padding-left:58px">
    <svg width="38" height="28" viewBox="0 0 38 28"><rect x="1" y="4" width="22" height="16" stroke="#1a1a1a" stroke-width="2" fill="none"/><path d="M23 9h8l5 6v5H23z" stroke="#1a1a1a" stroke-width="2" fill="none"/><circle cx="8" cy="22" r="3" fill="#fff" stroke="#1a1a1a" stroke-width="2"/><circle cx="29" cy="22" r="3" fill="#fff" stroke="#1a1a1a" stroke-width="2"/></svg>
    <div><h4>Payment Method</h4><p>Cash On Delivery</p></div>
  </div>

  <section class="abs brands" aria-label="Brands we carry"></section>
  <svg class="abs" style="left:80px;top:1558px" width="20" height="40"><path d="M18 1L2 20l16 19" stroke="#1a1a1a" stroke-width="2" fill="none"/></svg>
  <div class="abs mark" style="left:146px">Lunetto</div>
  <div class="abs mark" style="left:332px">Brevin</div>
  <div class="abs mark" style="left:516px">Castel</div>
  <div class="abs mark" style="left:696px">Marrow</div>
  <div class="abs mark" style="left:881px">Quillon</div>
  <svg class="abs" style="left:1103px;top:1558px" width="20" height="40"><path d="M2 1l16 19L2 39" stroke="var(--gold)" stroke-width="2" fill="none"/></svg>

  <h2 class="abs heading" style="top:1697px;font-weight:300">Subscribe For Our Newsletter</h2>
  <div class="abs rule" style="top:1734px;left:535px;width:133px"></div>
  <div class="abs news">E-Mail Address</div>
  <div class="abs send">
    <svg width="38" height="26" viewBox="0 0 38 26"><path d="M2 2l34 11L2 24l6-11z M8 13h28" stroke="#1a1a1a" stroke-width="2" fill="none" stroke-linejoin="round"/></svg>
  </div>
</main>

<footer>
  <div class="abs footer"></div>
  <div class="abs f-brand">ORLA</div>
  <p class="abs f-about">Lorem Ipsum is simply dummy text of the printing and typesetting industry.</p>
  <div class="abs" style="left:161px;top:2043px;font-size:10.5px;font-weight:400">READ MORE....</div>
  <div class="abs f-social" aria-label="Social links"><i></i><i></i><i></i><i></i><i></i></div>

  <div class="abs f-head" style="left:423px;top:1965px">QUICK LINK</div>
  <ul class="abs f-list" style="left:423px;top:2001px"><li>Women</li><li>Men</li><li>Youth</li><li>Collections</li><li>Contact Us</li></ul>

  <div class="abs f-head" style="left:635px;top:1965px">ACCOUNT</div>
  <ul class="abs f-list" style="left:635px;top:2001px"><li>My Account</li><li>My Wishlist</li><li>Checkout</li><li>Create Account</li><li>Register</li></ul>

  <div class="abs f-head" style="left:859px;top:1965px">QUICK CONTACT</div>
  <div class="abs f-contact" style="left:859px;top:2002px"><svg width="9" height="10" viewBox="0 0 10 10"><path d="M2 .5l2 2-1 1.3a6 6 0 0 0 3 3l1.3-1 2 2-1.3 1.7C4 9.5.5 6 .5 1.8z" fill="var(--gold)"/></svg>+012-555-310-7</div>
  <div class="abs f-contact" style="left:859px;top:2027px"><svg width="10" height="8"><rect width="10" height="8" fill="var(--gold)"/><path d="M0 0l5 4 5-4" stroke="#000" fill="none"/></svg>info@orlaoptica.com</div>
  <div class="abs f-contact" style="left:859px;top:2051px"><svg width="8" height="11" viewBox="0 0 8 11"><path d="M4 11S0 6 0 4a4 4 0 0 1 8 0c0 2-4 7-4 7z" fill="var(--gold)"/></svg><span>14 Linden Rd.<br>Harbor Falls, NJ 08120</span></div>

  <div class="abs divider"></div>
  <div class="abs copy" style="left:161px">CopyRight &nbsp;©2018 Orla Optica Medica. All Right Reserve</div>
  <div class="abs copy" style="left:820px">Privacy Policy - Terms &amp; Conditions</div>
</footer>

</body>
</html>
```